IT Company requires new Business Card design.

Over the years we have had a few different business card designs. We are now due for new cards across the board for all staff. We felt this would be a good time to start fresh with a new design. Our traditional card simply had our details on the front, and a list of services on the back. We don't particularly need the list of services, we have had cards where the only thing on the rear of the card was our logo.
Feel free to be creative, we would like our tag line "Complete IT Management" to appear at some point, doesn't necessarily have to be with the logo.
I have attached samples and drafts of various previous cards we have used over the years.

```html
<!DOCTYPE html>
<html lang="en">
<head>
<meta charset="utf-8">
<title>Harbour Systems – Business Card</title>
<link rel="stylesheet" href="https://fonts.googleapis.com/css2?family=Open+Sans:wght@400;600;700;800&display=swap">
<style>
  :root {
    --page-bg: #e6e4e1;
    --metal-dark: #1c1c1c;
    --metal-mid: #3a3a3a;
    --metal-light: #5a5a5a;
    --text-main: #ffffff;
    --text-soft: #e2e2e2;
    --rule: #8a8a8a;
    --mark: #bdbdbd;
  }
  * { margin: 0; padding: 0; box-sizing: border-box; }
  html, body { width: 1056px; height: 1200px; overflow: hidden; }
  body {
    background: var(--page-bg);
    font-family: "Open Sans", Arial, sans-serif;
    color: var(--text-main);
    position: relative;
  }
  .card {
    position: absolute;
    left: 88px;
    width: 880px;
    height: 500px;
    border-radius: 30px;
    overflow: hidden;
    background:
      repeating-linear-gradient(90deg, rgba(255,255,255,0.035) 0 1px, transparent 1px 3px, rgba(0,0,0,0.05) 3px 4px),
      linear-gradient(180deg, var(--metal-light) 0%, var(--metal-mid) 38%, var(--metal-dark) 100%);
  }
  .card--front { top: 70px; }
  .card--back { top: 630px; }

  .brand { position: absolute; display: flex; align-items: center; }
  .brand__square { background: var(--mark); flex: none; }
  .brand__name {
    font-weight: 800;
    color: var(--text-main);
    line-height: 0.95;
    letter-spacing: 1px;
  }
  .card--front .brand { left: 64px; top: 60px; gap: 26px; }
  .card--front .brand__square { width: 112px; height: 112px; }
  .card--front .brand__name { font-size: 58px; }
  .tagline {
    position: absolute;
    left: 202px; top: 196px;
    font-size: 15px;
    letter-spacing: 4.6px;
    color: var(--text-soft);
  }

  .divider {
    position: absolute; left: 0; right: 0; top: 332px;
    height: 3px; background: var(--rule);
  }
  .person { position: absolute; right: 56px; text-align: right; }
  .person__name { top: 282px; font-size: 28px; font-weight: 700; }
  .person__role { top: 346px; font-size: 21px; color: var(--text-soft); }

  .contacts { position: absolute; left: 60px; top: 360px; list-style: none; }
  .contacts li {
    display: flex; align-items: center; gap: 10px;
    height: 35px; font-size: 21px; color: var(--text-soft);
  }
  .contacts svg { width: 20px; height: 20px; flex: none; }
  .contacts .gap { margin-left: 18px; }

  .address {
    position: absolute; right: 56px; top: 424px;
    text-align: right; font-size: 21px; line-height: 33px; color: var(--text-soft);
  }

  .card--back .brand { left: 0; right: 0; top: 150px; justify-content: center; gap: 34px; }
  .card--back .brand__square { width: 150px; height: 150px; }
  .card--back .brand__name { font-size: 78px; }
  .web {
    position: absolute; left: 0; right: 0; top: 428px;
    text-align: center; font-size: 22px; letter-spacing: 3px; color: var(--text-soft);
  }
  .web strong { font-weight: 700; color: var(--text-main); }
</style>
</head>
<body>

<section class="card card--front">
  <div class="brand">
    <div class="brand__square"></div>
    <div class="brand__name">HARBOUR<br>SYSTEMS</div>
  </div>
  <div class="tagline">COMPLETE IT MANAGEMENT</div>

  <div class="person person__name">Marcus Hale</div>
  <div class="divider"></div>
  <div class="person person__role">Operation Manager</div>

  <ul class="contacts">
    <li>
      <svg viewBox="0 0 20 20" aria-hidden="true"><circle cx="10" cy="10" r="8.5" fill="none" stroke="#e2e2e2" stroke-width="1.6"/><path d="M7 5.5c-1 1-1 3 1 5.5s4.5 3 5.5 2l-1.6-1.8-1.4.8c-1-.6-2-1.6-2.6-2.6l.8-1.4z" fill="#e2e2e2"/></svg>
      08 9350 4418
      <svg class="gap" viewBox="0 0 20 20" aria-hidden="true"><rect x="5" y="1.5" width="10" height="17" rx="1.5" fill="none" stroke="#e2e2e2" stroke-width="1.6"/><rect x="7" y="4" width="6" height="6" fill="#e2e2e2"/><rect x="7" y="12" width="6" height="4" fill="#e2e2e2"/></svg>
      0412 738 905
    </li>
    <li>
      <svg viewBox="0 0 20 20" aria-hidden="true"><rect x="5" y="2" width="10" height="6" fill="#e2e2e2"/><rect x="2" y="8" width="16" height="8" rx="1.5" fill="#e2e2e2"/><rect x="5" y="13" width="10" height="5" fill="#e2e2e2" stroke="#333" stroke-width="1"/></svg>
      08 9350 4418
    </li>
    <li>
      <svg viewBox="0 0 20 20" aria-hidden="true"><path d="M2 8l8-5 8 5v9H2z" fill="#e2e2e2"/><path d="M2 8l8 5 8-5" fill="none" stroke="#333" stroke-width="1.4"/></svg>
      marcus@harboursystems.com.au
    </li>
    <li>
      <svg viewBox="0 0 20 20" aria-hidden="true"><circle cx="10" cy="10" r="8.5" fill="none" stroke="#e2e2e2" stroke-width="1.6"/><ellipse cx="10" cy="10" rx="3.5" ry="8.5" fill="none" stroke="#e2e2e2" stroke-width="1.4"/><path d="M1.5 10h17M3 5.5h14M3 14.5h14" stroke="#e2e2e2" stroke-width="1.4"/></svg>
      www.harboursystems.com.au
    </li>
  </ul>

  <address class="address" style="font-style:normal">
    Unit 4 18 Coral Reach<br>
    Bibra Lake WA 6163
  </address>
</section>

<section class="card card--back">
  <div class="brand">
    <div class="brand__square"></div>
    <div class="brand__name">HARBOUR<br>SYSTEMS</div>
  </div>
  <div class="web">www.<strong>harboursystems</strong>.com.au</div>
</section>

</body>
</html>
```